Business Card & Email Signature Design || Upmarket + Luxury

Rima Vale Honey, a New Zealand Manuka Honey company needs a Business Card & Email Signature design.

Our logo's are attached in Gold & Black versions, feel free to be creative with how you use the logo and it's patterns in your design.

Style:
- Looking for an Elegant, Luxurious, Upmarket feel.
- Black/Matte Black Card, Gold Foil, UV Embossing

Information to Add:

- Logo
- Company Name: Rima Vale Honey
- Name: Martin Holloway
- Title: Creative Director
- Phone: +64 2815 96 417
- Email: martin@rimavalehoney.example.nz
- Website: www.rimavalehoney.example.nz

- Socials: ***For email Signature Only***
- Facebook: https://www.facebook.com/rimavalehoney/
- Instagram: https://www.instagram.com/rimavalehoney/

Target Market(s)

Asia/Europe Luxury, Upmarket

Contact Information for Business Card

- Logo
- Name: Martin Holloway
- Phone: +64 2815 96 417

Font styles to use
Other font styles liked:
• Champagne & Limousines (Attached)

Requirements
Must have
• Business Card & Email Signature Design.

Looking for a Sleek, Luxury, Upmarket Design.

```html
<!DOCTYPE html>
<html lang="en">
<head>
<meta charset="utf-8">
<title>Rima Vale Honey — Business Card</title>
<link href="https://fonts.googleapis.com/css2?family=Josefin+Sans:wght@400&family=Arimo:wght@400;700&display=swap" rel="stylesheet">
<style>
  :root {
    --backdrop: #2a2a2b;
    --kraft-light: #dcb884;
    --kraft-mid: #c89d67;
    --kraft-dark: #b1834f;
    --ink: #1f1d1b;
    --ink-soft: #3a342d;
    --rule: #6e5a42;
  }
  * { box-sizing: border-box; margin: 0; padding: 0; }
  html, body {
    width: 1200px; height: 1015px; overflow: hidden;
    background: var(--backdrop);
  }
  .canvas {
    width: 1200px; height: 1015px;
    display: flex; flex-direction: column;
    align-items: center; justify-content: center; gap: 44px;
  }
  .card {
    width: 770px; height: 440px;
    background: linear-gradient(135deg, var(--kraft-light) 0%, var(--kraft-mid) 55%, var(--kraft-dark) 100%);
    color: var(--ink);
    position: relative;
    box-shadow: 0 12px 28px rgba(0,0,0,.45);
  }
  .brand-mark {
    width: 54px; height: 54px; border-radius: 50%;
    border: 2px solid var(--ink);
    flex: none;
  }
  .brand-name {
    font-family: "Josefin Sans", sans-serif;
    font-weight: 400;
    letter-spacing: .18em;
    text-transform: uppercase;
    color: var(--ink);
    white-space: nowrap;
  }

  /* Front */
  .card-front {
    display: flex; align-items: center; justify-content: center; gap: 26px;
  }
  .card-front .brand-name { font-size: 38px; }

  /* Back */
  .card-back {
    display: flex; align-items: center;
  }
  .card-back .brand-lockup {
    width: 400px;
    display: flex; flex-direction: column; align-items: center; gap: 22px;
  }
  .card-back .brand-name { font-size: 26px; }
  .divider {
    width: 1px; height: 150px; background: var(--rule);
  }
  .contact {
    padding-left: 34px;
    font-family: "Arimo", sans-serif;
    color: var(--ink-soft);
  }
  .contact-name {
    font-weight: 700; font-size: 24px; letter-spacing: .02em;
    text-transform: uppercase; color: var(--ink);
  }
  .contact-title { font-size: 17px; margin-bottom: 16px; }
  .contact-list { list-style: none; display: flex; flex-direction: column; gap: 7px; }
  .contact-list li {
    display: flex; align-items: center; gap: 10px; font-size: 15px;
  }
  .contact-list svg { width: 17px; height: 17px; flex: none; }
</style>
</head>
<body>
<main class="canvas">
  <section class="card card-front">
    <span class="brand-mark" aria-hidden="true"></span>
    <span class="brand-name">Rima Vale Honey</span>
  </section>

  <section class="card card-back">
    <div class="brand-lockup">
      <span class="brand-mark" aria-hidden="true"></span>
      <span class="brand-name">Rima Vale Honey</span>
    </div>
    <div class="divider"></div>
    <div class="contact">
      <p class="contact-name">Martin Holloway</p>
      <p class="contact-title">Creative Director</p>
      <ul class="contact-list">
        <li>
          <svg viewBox="0 0 24 24" aria-hidden="true"><path fill="#1f1d1b" d="M6.6 10.8a15.1 15.1 0 0 0 6.6 6.6l2.2-2.2c.3-.3.7-.4 1-.2 1.1.4 2.3.6 3.6.6.6 0 1 .4 1 1V20c0 .6-.4 1-1 1A17 17 0 0 1 3 4c0-.6.4-1 1-1h3.5c.6 0 1 .4 1 1 0 1.3.2 2.5.6 3.6.1.3 0 .7-.2 1z"/></svg>
          +64 2815 96 417
        </li>
        <li>
          <svg viewBox="0 0 24 24" aria-hidden="true"><path fill="#1f1d1b" d="M2 5h20v14H2z"/><path fill="none" stroke="#c89d67" stroke-width="1.6" d="M2.5 5.5 12 13l9.5-7.5"/></svg>
          martin@rimavalehoney.example.nz
        </li>
        <li>
          <svg viewBox="0 0 24 24" aria-hidden="true"><g fill="none" stroke="#1f1d1b" stroke-width="1.8"><circle cx="12" cy="12" r="9.5"/><ellipse cx="12" cy="12" rx="4" ry="9.5"/><path d="M2.5 12h19M4 7h16M4 17h16"/></g></svg>
          www.rimavalehoney.example.nz
        </li>
      </ul>
    </div>
  </section>
</main>
</body>
</html>
```